Counseling Practice Business Card

I need a professional looking business card incorporating my new logo that was just completed. Card needs to incorporate my name and title, description of my specialty, my address, my phone number, my fax number, my email and my website URL. I need to be able to choose design on/with different paper colors and textures.
I do not have a lot of business card ideas so I am open to anything but I want bold,sharp, clear card without additional designs other than my logo (see attached file info). I am open to different color backgrounds or paper colors including black. I do not like traditional brackets around area codes in phone number or dashes between numbers in phone number. Am open to other ways of presenting including periods between numbers as appropriate. I do not know enough to know what I like yet but I want card to coordinate and work together with my logo. My practice emphasizes natural mental health interventions so any use of color (with background paper color or the blue and green in my logo) that elicits nature is nice. In addition to black, any natural brown or wood looking background might be desirable also. Most of the offerings so far look very similar and boring.

Target Market(s)

Potential therapy clients and other professionals

Contact Information for Business Card

Card information:
Gerald M. Whitcombe, Ph.D.
Licensed Clinical Psychologist
Integrative Health Coach
4812 Marlowe Ridge Blvd SE
Suite 310
Fernhollow, GA 30412
(770) 415-2983 phone
(770) 581-4096 fax
drgeraldwhitcombe@quillmarsh.net
brightfernwellness.net

Font styles to use
Serif
Sans Serif
Other font styles liked:
• anything that you think looks crisp, clear and easily readable

Requirements
Must have
• Any color used should coordinate with my logo design (see attached files).
• Card should be printed horizontally so top and bottom are longest sides of rectangle.
• Background color or paper color should complement and highlight logo. Do not like a white background. black, grey, brown or any color my logo would blend well with.
Nice to have
• I would like designer to utilize color to highlight letters/name or phone-fax-web symbols.
• Bottom edge of card could be highlighted if appropriate to an idea.
Should not have
• I would NOT want the card to have a pure white background at all.
• No clear cards.
• Cards should be oriented with long sides on bottom and top, NOT sides. DO NOT LIKE THIS THIN TALL ORIENTATION.

```html
<!DOCTYPE html>
<html lang="en">
<head>
<meta charset="utf-8">
<title>Brightfern Wellness – Business Card</title>
<link href="https://fonts.googleapis.com/css2?family=Roboto:wght@400;500;700&display=swap" rel="stylesheet">
<style>
  :root {
    --backdrop: #1c1c1c;
    --card: #242424;
    --card-edge: #2e2e2e;
    --emboss: #3e3e3e;
    --foil: #d6d6d6;
    --foil-soft: #a9a9a9;
    --rule: #5a5a5a;
  }
  html, body {
    margin: 0;
    padding: 0;
    width: 1200px;
    height: 900px;
    overflow: hidden;
    background: var(--backdrop);
    font-family: "Roboto", Arial, sans-serif;
  }
  .canvas {
    position: relative;
    width: 1200px;
    height: 900px;
  }
  .card {
    position: absolute;
    left: 320px;
    width: 560px;
    height: 320px;
    background: linear-gradient(160deg, var(--card-edge), var(--card) 60%);
    box-shadow: 0 10px 28px rgba(0,0,0,0.55);
  }
  .card-front { top: 100px; }
  .card-back { top: 470px; }

  .brand {
    position: absolute;
    inset: 0;
    display: flex;
    align-items: center;
    justify-content: center;
    gap: 14px;
  }
  .brand-dot {
    width: 14px;
    height: 14px;
    border-radius: 50%;
    background: var(--foil);
  }
  .brand-name {
    font-size: 40px;
    font-weight: 500;
    color: var(--foil);
    letter-spacing: 1px;
  }

  .identity {
    position: absolute;
    right: 308px;
    top: 78px;
    text-align: right;
    color: var(--emboss);
  }
  .identity-name {
    font-size: 18px;
    font-weight: 700;
    margin: 0 0 6px;
    white-space: nowrap;
  }
  .identity-title {
    font-size: 14px;
    font-weight: 500;
    margin: 0 0 3px;
    white-space: nowrap;
  }
  .divider {
    position: absolute;
    left: 266px;
    top: 74px;
    width: 1px;
    height: 88px;
    background: var(--rule);
  }
  .contact {
    position: absolute;
    left: 282px;
    top: 76px;
    margin: 0;
    padding: 0;
    list-style: none;
    color: var(--foil);
    font-size: 14px;
    line-height: 21px;
  }
  .contact li {
    display: flex;
    align-items: center;
    gap: 9px;
    white-space: nowrap;
  }
  .contact svg {
    width: 11px;
    height: 11px;
    fill: none;
    stroke: var(--foil-soft);
    stroke-width: 1.4;
  }
  .address {
    position: absolute;
    left: 44px;
    bottom: 52px;
    margin: 0;
    font-size: 15px;
    font-weight: 500;
    color: var(--foil-soft);
    white-space: nowrap;
  }
  .address .street { color: var(--emboss); }
</style>
</head>
<body>
<main class="canvas">
  <section class="card card-front" aria-label="Card front">
    <div class="brand">
      <span class="brand-dot"></span>
      <span class="brand-name">Brightfern Wellness</span>
    </div>
  </section>

  <section class="card card-back" aria-label="Card back">
    <div class="identity">
      <p class="identity-name">Gerald M. Whitcombe, Ph.D.</p>
      <p class="identity-title">Licensed Clinical Psychologist</p>
      <p class="identity-title">Integrative Health Coach</p>
    </div>
    <div class="divider"></div>
    <ul class="contact">
      <li>
        <svg viewBox="0 0 12 12"><path d="M3 1 L4.5 3.5 L3.5 4.5 Q5 7.5 7.5 8.5 L8.5 7.5 L11 9 L10 11 Q3 10 1 2 Z"/></svg>
        (770) 415-2983
      </li>
      <li>
        <svg viewBox="0 0 12 12"><rect x="3" y="1" width="6" height="3"/><rect x="1" y="4" width="10" height="5"/><rect x="3" y="8" width="6" height="3"/></svg>
        (770) 581-4096
      </li>
      <li>
        <svg viewBox="0 0 12 12"><rect x="1" y="2.5" width="10" height="7"/><path d="M1 2.5 L6 6.5 L11 2.5"/></svg>
        drgeraldwhitcombe@quillmarsh.net
      </li>
      <li>
        <svg viewBox="0 0 12 12"><circle cx="6" cy="6" r="5"/><ellipse cx="6" cy="6" rx="2.2" ry="5"/><path d="M1 6 H11"/></svg>
        www.brightfernwellness.net
      </li>
    </ul>
    <p class="address"><span class="street">4812 Marlowe Ridge Blvd SE</span> Suite 310 Fernhollow, GA 30412</p>
  </section>
</main>
</body>
</html>
```